Business card for Eyelash extension salon in Beverly Hills,California USA

We need new business card for our salon in Beverly Hills. The salon name is 'Lashvera' . We would like to have...Business name: Lashvera Name of person: will provide later Address 4720 N.Alder Crest Ave Beverly Hills , CA 90210 Phone: will provide later (Text only) Web: www.lashverastudio.example Snapgrid icon, Circlebook icon follow us for seasonal campaign and news @lashverastudiolounge Design should look elegant, high-end, clean, simple, cohesive with my brand. Please refer my brand board. Business name color will be metallic bronzy color. Im thinking grey background or white background. Thanks

Target Market(s)

25-35. Gender neutral. People who are in Entertainment business industry.
This is High-end Eyelash extension salon in Beverly Hills

Industry/Entity Type

Beauty Salon

Contact Information for Business Card

Business name: Lashvera
Name of person: will provide later
Address 4720 N.Alder Crest Ave Beverly Hills , CA 90210
Phone: will provide later (Text only)
Web: www.lashverastudio.example
Snapgrid icon, Circlebook icon
follow us for seasonal campaign and news @lashverastudiolounge

Requirements
Must have
• Beautiful, elegant, clean and simple look but very attractive and modern
Should not have
• We don't like too clutter, too busy designs.

```html
<!DOCTYPE html>
<html lang="en">
<head>
<meta charset="utf-8">
<title>Lashvera Business Card</title>
<link rel="stylesheet" href="https://fonts.googleapis.com/css2?family=Arimo:wght@400&family=Libre+Caslon+Text:wght@700&display=swap">
<style>
  :root {
    --backdrop: #8d8e90;
    --card-grey: #ecebe8;
    --card-grey-deep: #dedcd8;
    --foil-bronze: #9c7b57;
    --text-dark: #4a4845;
    --text-muted: #7a7672;
    --rule-line: #b39b7d;
  }
  * { margin: 0; padding: 0; box-sizing: border-box; }
  html, body {
    width: 1200px;
    height: 800px;
    overflow: hidden;
    background: var(--backdrop);
  }
  .canvas {
    position: relative;
    width: 1200px;
    height: 800px;
    display: flex;
    align-items: center;
    justify-content: center;
  }
  .business-card {
    position: relative;
    width: 1000px;
    height: 572px;
    background: radial-gradient(ellipse at 40% 35%, var(--card-grey) 0%, var(--card-grey-deep) 100%);
    box-shadow: 0 18px 40px rgba(0, 0, 0, 0.3);
    font-family: "Arimo", Arial, sans-serif;
  }
  .brand {
    position: absolute;
    top: 70px;
    right: 92px;
    text-align: right;
  }
  .brand-name {
    font-family: "Arimo", Arial, sans-serif;
    font-weight: 400;
    font-size: 62px;
    letter-spacing: 2px;
    color: var(--foil-bronze);
    line-height: 1;
  }
  .brand-place {
    margin-top: 10px;
    font-size: 13px;
    letter-spacing: 4px;
    color: var(--foil-bronze);
    text-transform: uppercase;
  }
  .divider-top {
    position: absolute;
    top: 262px;
    left: 70px;
    right: 70px;
    height: 1.5px;
    background: var(--rule-line);
  }
  .person {
    position: absolute;
    top: 288px;
    left: 70px;
  }
  .person-name {
    font-family: "Libre Caslon Text", "Times New Roman", serif;
    font-weight: 700;
    font-size: 30px;
    letter-spacing: 0.5px;
    color: var(--foil-bronze);
    text-transform: uppercase;
  }
  .person-role {
    margin-top: 6px;
    font-size: 20px;
    color: var(--text-muted);
  }
  .divider-short {
    position: absolute;
    top: 376px;
    left: 70px;
    width: 480px;
    height: 1.5px;
    background: var(--rule-line);
  }
  .contact-list {
    position: absolute;
    top: 396px;
    left: 70px;
    right: 70px;
    list-style: none;
    font-size: 20px;
    line-height: 40px;
    color: var(--text-dark);
    white-space: nowrap;
  }
  .contact-label {
    color: var(--foil-bronze);
    margin-right: 6px;
  }
  .contact-gap { display: inline-block; width: 22px; }
  .social-line {
    font-size: 18px;
    color: var(--text-muted);
  }
  .social-dot {
    display: inline-block;
    width: 12px;
    height: 12px;
    border-radius: 50%;
    background: var(--foil-bronze);
    margin-right: 7px;
    vertical-align: -1px;
  }
  .social-name { color: var(--text-dark); }
  .social-handle { color: var(--foil-bronze); }
</style>
</head>
<body>
<main class="canvas">
  <section class="business-card" aria-label="Lashvera business card">
    <div class="brand">
      <div class="brand-name">Lashvera</div>
      <div class="brand-place">Beverly Hills</div>
    </div>

    <div class="divider-top"></div>

    <div class="person">
      <p class="person-name">Adrian Vale</p>
      <p class="person-role">Makeup Artist</p>
    </div>

    <div class="divider-short"></div>

    <ul class="contact-list">
      <li>
        <span class="contact-label">A:</span><span class="contact-value">4720 N.Alder Crest Ave Beverly Hills , CA 90210</span>
      </li>
      <li>
        <span class="contact-label">E:</span><span class="contact-value">info@lashverastudio.example</span><span class="contact-gap"></span><span class="contact-label">T:</span><span class="contact-value">503-555-0142</span><span class="contact-gap"></span><span class="contact-label">W:</span><span class="contact-value">www.lashverastudio.example</span>
      </li>
      <li class="social-line">
        <span class="social-dot"></span><span class="social-name">Snapgrid</span><span class="contact-gap"></span><span class="social-dot"></span><span class="social-name">Circlebook</span><span class="contact-gap"></span>Follow us for seasonal campaign and news <span class="social-handle">@lashverastudiolounge</span>
      </li>
    </ul>
  </section>
</main>
</body>
</html>
```